Need Business Card for our Real Estate Business with Sales Executive's Picture

PANTONE 484 C ( RED)

PANTONE 2766 C ( BLUE

Industry/Entity Type

Real Estate

Contact Information for Business Card

Name, Mobile, email, & picture of Person
Agency Phone, address, Web address

Requirements
Must have
• Our Logo Colours, Agent Picture,

```html
<!DOCTYPE html>
<html lang="en">
<head>
<meta charset="utf-8">
<title>Meridan Real Estate – Business Card</title>
<link rel="stylesheet" href="https://fonts.googleapis.com/css2?family=Open+Sans:wght@400;600&display=swap">
<style>
  :root {
    --backdrop: #cfd2d5;
    --paper: #ffffff;
    --navy: #061538;
    --slate: #666a80;
    --ink: #3c3c3c;
    --ink-soft: #6b6b6b;
    --rule: #9a9a9a;
    --brand-red: #9a3324;
    --photo-dark: #1f3a7a;
    --photo-light: #d9d2cc;
  }
  * { box-sizing: border-box; margin: 0; padding: 0; }
  html, body {
    width: 1200px; height: 1000px; overflow: hidden;
    background: var(--backdrop);
    font-family: "Open Sans", sans-serif;
  }
  .card {
    position: absolute;
    width: 682px; height: 389px;
    background: var(--paper);
    overflow: hidden;
  }
  .card--front { left: 262px; top: 85px; }
  .card--back  { left: 261px; top: 525px; background: var(--navy); }
  .card svg.shape { position: absolute; inset: 0; width: 100%; height: 100%; }

  .agent-photo {
    position: absolute; left: 36px; top: 30px;
    width: 168px; height: 226px;
    background: linear-gradient(180deg, var(--photo-light) 0%, var(--photo-light) 30%, var(--photo-dark) 45%, var(--photo-dark) 100%);
  }
  .identity { position: absolute; left: 212px; top: 38px; width: 434px; }
  .identity__name { font-size: 25px; color: var(--ink); line-height: 1.2; }
  .identity__title { font-size: 19px; color: var(--ink); line-height: 1.3; }
  .identity__rule { border: 0; border-top: 1.5px solid var(--rule); margin: 14px 0 12px; }
  .identity__address { font-size: 19px; color: var(--ink-soft); }

  .contacts { position: absolute; left: 286px; top: 256px; list-style: none; }
  .contacts li {
    display: flex; align-items: center; gap: 14px;
    height: 37px; font-size: 19px; color: var(--paper);
  }
  .contacts svg { width: 20px; height: 20px; }

  .brand-name { position: absolute; color: var(--paper); font-weight: 600; text-align: center; }
  .card--front .brand-name { left: 53px; top: 300px; width: 160px; font-size: 22px; letter-spacing: 2px; }
  .card--back .brand-name { left: 0; top: 195px; width: 682px; font-size: 44px; letter-spacing: 5px; }
  .brand-square {
    position: absolute; left: 333px; top: 160px;
    width: 16px; height: 16px; background: var(--brand-red);
  }
</style>
</head>
<body>

<section class="card card--front">
  <svg class="shape" viewBox="0 0 682 389" aria-hidden="true">
    <path d="M0,236 C110,268 260,262 390,212 C490,176 600,164 682,176 L682,389 L0,389 Z" fill="var(--navy)"/>
  </svg>
  <div class="agent-photo" role="img" aria-label="Portrait of the sales executive in a navy suit"></div>

  <div class="identity">
    <p class="identity__name">Name of Sales Executive's</p>
    <p class="identity__title">Sales Executive</p>
    <hr class="identity__rule">
    <p class="identity__address">address of Meridan Real Estate</p>
  </div>

  <ul class="contacts">
    <li>
      <svg viewBox="0 0 20 20" fill="none" stroke="#fff" stroke-width="1.6"><circle cx="10" cy="10" r="8"/><path d="M7 6.5 l1.5 -0.5 l1 2 l-1 1 q1 2 2.5 2.5 l1 -1 l2 1 l-0.5 1.5 q-5 0 -6.5 -6.5z" fill="#fff" stroke="none"/></svg>
      <span>mobile / agency phone</span>
    </li>
    <li>
      <svg viewBox="0 0 20 20" fill="none" stroke="#fff" stroke-width="1.6"><rect x="3" y="5" width="14" height="10"/><path d="M3 5 l7 6 l7 -6"/></svg>
      <span>meridan@email.com</span>
    </li>
    <li>
      <svg viewBox="0 0 20 20" fill="none" stroke="#fff" stroke-width="1.5"><circle cx="10" cy="10" r="8"/><ellipse cx="10" cy="10" rx="3.5" ry="8"/><path d="M2 10 h16 M3.5 6 h13 M3.5 14 h13"/></svg>
      <span>www.web address.com</span>
    </li>
  </ul>

  <p class="brand-name">MERIDAN</p>
</section>

<section class="card card--back">
  <svg class="shape" viewBox="0 0 682 389" aria-hidden="true">
    <path d="M0,180 C150,330 330,345 470,320 C580,300 640,240 682,180 L682,389 L0,389 Z" fill="var(--slate)"/>
    <path d="M0,260 C150,340 320,350 470,330 C580,312 650,250 682,190 L682,389 L0,389 Z" fill="var(--paper)"/>
  </svg>
  <div class="brand-square"></div>
  <p class="brand-name">MERIDAN</p>
</section>

</body>
</html>
```